Marlowe Group needs a business card

I would like the card to be simple but modern and elegant.
I like black and white.
or black and gold.
we are a private finance lender and also are involved in property and property developments.

please look at the business card photos i provided i would like M.G only one one side and all the other details on the other side use fonts that tie in with my theme.

Industry/Entity Type

Finance

Contact Information for Business Card

Marlowe Group (M.G) Daniel Marlowe M: 0413586207 E: danmarl@inboxmail.test

Font styles to use
Other font styles liked:
• Use fonts that would reflect our business

Colors
000000
ffffff

Requirements
Must have
• one side of details
• other side has either M.G or Marlowe Group like in the photos provided

```html
<!DOCTYPE html>
<html lang="en">
<head>
<meta charset="utf-8">
<title>Marlowe Group — Business Card</title>
<link rel="stylesheet" href="https://fonts.googleapis.com/css2?family=Open+Sans:wght@400;600&display=swap">
<style>
  :root {
    --page: #d9d7d4;
    --card: #16191d;
    --card-edge: #0c0e10;
    --ink: #f2f2f2;
    --ink-soft: #d8d8d8;
    --accent-bar: #ffffff;
  }
  * { box-sizing: border-box; margin: 0; padding: 0; }
  html, body {
    width: 1200px;
    height: 769px;
    overflow: hidden;
    background: var(--page);
    font-family: "Open Sans", Arial, sans-serif;
  }
  .sheet {
    position: relative;
    width: 1200px;
    height: 769px;
    display: flex;
    align-items: center;
    justify-content: center;
    gap: 50px;
  }
  .card {
    position: relative;
    width: 520px;
    height: 300px;
    background: var(--card);
    border-radius: 4px;
    box-shadow: 0 2px 0 var(--card-edge);
    overflow: hidden;
  }
  /* Details side */
  .card--details .side-bar {
    position: absolute;
    left: 16px;
    top: 168px;
    width: 14px;
    height: 118px;
    background: var(--accent-bar);
    border-radius: 3px 3px 7px 3px;
  }
  .card--details .contact {
    position: absolute;
    left: 48px;
    top: 168px;
    color: var(--ink);
  }
  .contact .person-name {
    font-size: 21px;
    font-weight: 600;
    letter-spacing: 0.2px;
    margin-bottom: 14px;
  }
  .contact ul { list-style: none; }
  .contact li {
    display: flex;
    align-items: center;
    gap: 10px;
    font-size: 15.5px;
    font-weight: 400;
    color: var(--ink-soft);
    line-height: 24px;
  }
  .contact .icon {
    width: 16px;
    height: 16px;
    flex: none;
  }
  /* Company name side */
  .card--brand {
    display: flex;
    align-items: center;
    justify-content: center;
  }
  .card--brand .company-name {
    font-size: 30px;
    font-weight: 600;
    color: var(--ink);
    white-space: nowrap;
    transform: translate(30px, -40px);
  }
</style>
</head>
<body>
  <main class="sheet">
    <section class="card card--details" aria-label="Contact side">
      <div class="side-bar"></div>
      <div class="contact">
        <p class="person-name">Daniel Marlowe</p>
        <ul>
          <li>
            <svg class="icon" viewBox="0 0 16 16" aria-hidden="true">
              <rect x="4" y="1" width="8" height="14" rx="1.5" fill="none" stroke="#e6e6e6" stroke-width="1.4"/>
              <line x1="7" y1="12.5" x2="9" y2="12.5" stroke="#e6e6e6" stroke-width="1.2"/>
            </svg>
            0413586207
          </li>
          <li>
            <svg class="icon" viewBox="0 0 16 16" aria-hidden="true">
              <rect x="1.5" y="3.5" width="13" height="9" fill="#e6e6e6"/>
              <polyline points="1.5,3.5 8,9 14.5,3.5" fill="none" stroke="#16191d" stroke-width="1.3"/>
            </svg>
            danmarl@inboxmail.test
          </li>
          <li>
            <svg class="icon" viewBox="0 0 16 16" aria-hidden="true">
              <circle cx="8" cy="8" r="7" fill="#e6e6e6"/>
              <ellipse cx="8" cy="8" rx="3" ry="7" fill="none" stroke="#16191d" stroke-width="1"/>
              <line x1="1" y1="8" x2="15" y2="8" stroke="#16191d" stroke-width="1"/>
            </svg>
            www.marlowegroup.com
          </li>
        </ul>
      </div>
    </section>

    <section class="card card--brand" aria-label="Company side">
      <span class="company-name">Marlowe Group</span>
    </section>
  </main>
</body>
</html>
```